Business Card Design for Marketing Firm

Looking for business card design for higher end marketing firm. Clean but impressionable/trendy. We are a marketing firm that represents manufacturers in the foodservice equipment and supply industry. Our customers are end users such has hotels, restaurants, country clubs, convention centers and casinos as well as distributors of restaurants supplies and equipment, and manufacturers of foodservice equipment and supplies.
Target Market(s)
Hotels, Restaurants, Supply & Equipment Distributors, Foodservice Manufacturers
Industry/Entity Type
Foodservice/Hospitality
Contact Information for Business Card
Name, Title, Contact Number, Email, Website, Social Media, Address
Requirements
Must have
- Clean & Simple but Serious and Impressionable

```html
<!DOCTYPE html>
<html lang="en">
<head>
<meta charset="utf-8">
<title>Meridian Hospitality Reps – Business Card</title>
<link rel="stylesheet" href="https://fonts.googleapis.com/css2?family=Cinzel:wght@500&family=Poppins:wght@400;500&display=swap">
<style>
  :root {
    --backdrop: #3b3b3d;
    --card-white: #ffffff;
    --brand-blue: #00087f;
    --ink-white: #ffffff;
    --serif: "Cinzel", serif;
    --sans: "Poppins", sans-serif;
  }
  * { margin: 0; padding: 0; box-sizing: border-box; }
  html, body { width: 1200px; height: 689px; overflow: hidden; background: var(--backdrop); }
  .canvas { position: relative; width: 1200px; height: 689px; }

  .card {
    position: absolute; top: 190px; width: 540px; height: 310px;
    border-radius: 22px; overflow: hidden;
    box-shadow: 0 14px 30px rgba(0,0,0,.35);
  }
  .card--front { left: 40px; background: var(--card-white); }
  .card--back { left: 620px; background: var(--brand-blue); color: var(--ink-white); }

  .brand {
    position: absolute; display: flex; align-items: center;
    font-family: var(--sans); font-weight: 500; white-space: nowrap; line-height: 1;
  }
  .brand__mark { flex: none; border-radius: 50%; background: currentColor; }

  .card--front .brand {
    left: 50%; top: 50%; transform: translate(-50%, -50%);
    color: var(--brand-blue); font-size: 26px; gap: 14px;
  }
  .card--front .brand__mark { width: 30px; height: 30px; }

  .card--back .brand {
    left: 34px; top: 146px; color: var(--ink-white); font-size: 14.5px; gap: 9px;
  }
  .card--back .brand__mark { width: 18px; height: 18px; }

  .contact { position: absolute; left: 300px; top: 52px; font-family: var(--sans); }
  .contact__name { font-family: var(--serif); font-size: 17px; font-weight: 500; letter-spacing: .03em; line-height: 1.1; }
  .contact__title { font-size: 12px; margin-bottom: 16px; }
  .contact__list { list-style: none; font-size: 11.5px; line-height: 1.35; }
  .contact__item { display: flex; align-items: flex-start; gap: 7px; white-space: nowrap; }
  .contact__item svg { width: 11px; height: 11px; margin-top: 3px; flex: none; }
  .contact__item--address { margin-top: 12px; }

  .social { position: absolute; right: 40px; top: 238px; display: flex; gap: 7px; }
  .social__dot { width: 15px; height: 15px; border: 1px solid var(--ink-white); border-radius: 50%; }
  .divider { position: absolute; left: 300px; bottom: 36px; width: 92px; height: 1.5px; background: var(--ink-white); }
</style>
</head>
<body>
<main class="canvas">
  <section class="card card--front" aria-label="Card front">
    <div class="brand">
      <span class="brand__mark"></span>
      <span class="brand__name">Meridian Hospitality Reps</span>
    </div>
  </section>

  <section class="card card--back" aria-label="Card back">
    <div class="brand">
      <span class="brand__mark"></span>
      <span class="brand__name">Meridian Hospitality Reps</span>
    </div>

    <div class="contact">
      <p class="contact__name">DORIAN HALE</p>
      <p class="contact__title">Managing Director</p>
      <ul class="contact__list">
        <li class="contact__item">
          <svg viewBox="0 0 12 12" fill="none" stroke="#fff" stroke-width="1.3"><path d="M2.5 1.5h2l1 2.5-1.3 1a6 6 0 0 0 2.8 2.8l1-1.3 2.5 1v2a1 1 0 0 1-1 1A9 9 0 0 1 1.5 2.5a1 1 0 0 1 1-1z"/></svg>
          <span>055-210 384 617</span>
        </li>
        <li class="contact__item">
          <svg viewBox="0 0 12 12" fill="none" stroke="#fff" stroke-width="1.2"><rect x="1" y="2.5" width="10" height="7"/><path d="M1 2.5l5 4 5-4"/></svg>
          <span>hello@meridianreps.com</span>
        </li>
        <li class="contact__item">
          <svg viewBox="0 0 12 12" fill="none" stroke="#fff" stroke-width="1"><circle cx="6" cy="6" r="5"/><ellipse cx="6" cy="6" rx="2.2" ry="5"/><path d="M1 6h10"/></svg>
          <span>www.meridianreps.com</span>
        </li>
        <li class="contact__item contact__item--address">
          <svg viewBox="0 0 12 12" fill="#fff"><path d="M6 0.5a4 4 0 0 1 4 4c0 3-4 7-4 7s-4-4-4-7a4 4 0 0 1 4-4z"/><circle cx="6" cy="4.5" r="1.4" fill="#00087f"/></svg>
          <span>48, Harbor Lane<br>Region name, 560210</span>
        </li>
      </ul>
    </div>

    <div class="social" aria-label="Social profiles">
      <span class="social__dot"></span>
      <span class="social__dot"></span>
      <span class="social__dot"></span>
      <span class="social__dot"></span>
    </div>
    <span class="divider"></span>
  </section>
</main>
</body>
</html>
```